Structural Engineering Business Card

Brookvane Drafting does residential house plans for clients in Central Florida. Would like simple but elegant business card that is appropriate for a house plan engineering company. Prefer black business card with black/white them but open to other shades of blue. I uploaded a sample card that I came across that looked good but please come up with your own creative designs.

Contact Information for Business Card

Name, Title, Phone, Email, Address, website

```html
<!DOCTYPE html>
<html lang="en">
<head>
<meta charset="utf-8">
<title>Brookvane Drafting – Business Card</title>
<link href="https://fonts.googleapis.com/css2?family=Poppins:wght@400;600;700&display=swap" rel="stylesheet">
<style>
  :root {
    --stage: #6a6a6a;
    --card-front: #ffffff;
    --card-back: #1f2b36;
    --ink: #111111;
    --ink-soft: #3a3a3a;
    --divider: #9a9a9a;
    --back-mark: #56636f;
  }
  * { box-sizing: border-box; margin: 0; padding: 0; }
  html, body { width: 1093px; height: 1200px; overflow: hidden; }
  body {
    background: var(--stage);
    font-family: "Poppins", sans-serif;
    position: relative;
  }
  .card {
    position: absolute;
    left: 265px;
    width: 577px;
    height: 356px;
    border-radius: 22px;
  }
  .card--front { top: 226px; background: var(--card-front); }
  .card--back { top: 621px; background: var(--card-back); }

  .brand-name {
    position: absolute;
    left: 44px;
    top: 162px;
    width: 230px;
    text-align: center;
    font-weight: 700;
    font-size: 22px;
    color: var(--ink);
    white-space: nowrap;
  }
  .divider {
    position: absolute;
    left: 289px;
    top: 74px;
    width: 1px;
    height: 209px;
    background: linear-gradient(to bottom, transparent, var(--divider) 20%, var(--divider) 80%, transparent);
  }
  .details { position: absolute; left: 311px; top: 90px; color: var(--ink); }
  .person-name { font-weight: 700; font-size: 20px; line-height: 22px; letter-spacing: 0.2px; }
  .person-title { font-size: 16px; line-height: 20px; color: var(--ink-soft); }
  .contact-list { list-style: none; margin-top: 13px; }
  .contact-item {
    display: flex; align-items: center; gap: 8px;
    font-size: 16.5px; line-height: 21px;
  }
  .contact-item svg { width: 14px; height: 14px; flex: none; }
  .address { margin-top: 13px; font-size: 16.5px; line-height: 21px; }

  .back-name {
    position: absolute;
    left: 0; right: 0;
    top: 152px;
    text-align: center;
    font-weight: 700;
    font-size: 36px;
    color: var(--back-mark);
    white-space: nowrap;
  }
</style>
</head>
<body>
  <section class="card card--front">
    <div class="brand-name">Brookvane Drafting</div>
    <div class="divider"></div>
    <div class="details">
      <p class="person-name">DANIEL WHITMORE</p>
      <p class="person-title">Managing Director</p>
      <ul class="contact-list">
        <li class="contact-item">
          <svg viewBox="0 0 24 24" aria-hidden="true"><path fill="currentColor" d="M6.6 10.8a15 15 0 0 0 6.6 6.6l2.2-2.2a1 1 0 0 1 1-.25 11.4 11.4 0 0 0 3.6.57 1 1 0 0 1 1 1V20a1 1 0 0 1-1 1A17 17 0 0 1 3 4a1 1 0 0 1 1-1h3.5a1 1 0 0 1 1 1c0 1.25.2 2.45.57 3.6a1 1 0 0 1-.25 1z"/></svg>
          044-987 650 312
        </li>
        <li class="contact-item">
          <svg viewBox="0 0 24 24" aria-hidden="true"><path fill="currentColor" d="M2 5h20v14H2zm2 2v.5l8 5 8-5V7l-8 5z"/></svg>
          info@brookvane.com
        </li>
        <li class="contact-item">
          <svg viewBox="0 0 24 24" aria-hidden="true"><g fill="none" stroke="currentColor" stroke-width="2"><circle cx="12" cy="12" r="10"/><ellipse cx="12" cy="12" rx="4" ry="10"/><path d="M2 12h20M4 7h16M4 17h16"/></g></svg>
          www.brookvane.com
        </li>
      </ul>
      <p class="address">421, Address line goes here<br>45452,Country Name</p>
    </div>
  </section>

  <section class="card card--back">
    <div class="back-name">Brookvane Drafting</div>
  </section>
</body>
</html>
```